Business Card Design

We, Corvane Capital Partners, LLC, are financial Advisors, wealth management firm who works with individuals, families, senior level executives and small businesses in accomplishing their investment and retirement goals.

Our mission is to serve as a trusted advisor for all aspects of our clients’ financial lives. To do this, we take the time to develop a detailed understanding of each client’s individual circumstances, goals, and objectives. We help our clients make smart financial and investment decisions, and gain confidence in having a secure financial future.

We recommend financial products/services that best suit our client's goals.

Target Market(s)

high net worth individuals, families, senior level executives and small businesses

Industry/Entity Type

Investment

Contact Information for Business Card

R. Daniel Hollis
Principal, Financial Advisor, WPSA®
Corvane Capital Partners, LLC
418 Brenton Street, Suite 2300
New York, NY 10027

Email: dan@corvanecapital.example
website: www.corvanecapital.example

Phone: 646-555-0192
Office: 646-555-0148
Toll-Free 800-555-0176
Fax: 646-555-0133

Requirements
Must have
• I'm a financial advisor , so I need a strong appearance. Key words: wealth management, Investment returns, security, integrity, financial guidance, success, professional, traditional, conservative.

Put ALL my info in your draft, not just generic "john smith"... I want to see my info...

Business card must be more traditional in nature, tad conservative. Don't make it flashy, fancy or full of arcs (besides my logo) and curves. I am in a conservative business, so less is more.

Next to my name must be my titles: Principal, Financial Advisor, WPSA®
Also, next to the "WPSA", put the "®" Don't forget the commas!
Should not have
• curves, flashes,

```html
<!DOCTYPE html>
<html lang="en">
<head>
<meta charset="utf-8">
<title>Corvane Capital Partners, LLC – Business Card</title>
<link rel="stylesheet" href="https://fonts.googleapis.com/css2?family=Exo+2:wght@400;600&display=swap">
<style>
  :root {
    --backdrop: #2a2b2d;
    --card: #f4f5f6;
    --card-edge: #e2e4e6;
    --navy: #1f4a7e;
    --ink: #3a3d42;
    --rule: #8d9196;
    --icon: #2f3338;
  }
  * { box-sizing: border-box; margin: 0; padding: 0; }
  html, body { width: 1200px; height: 754px; overflow: hidden; }
  body {
    background: var(--backdrop);
    font-family: "Exo 2", sans-serif;
    position: relative;
  }
  .card {
    position: absolute;
    top: 212px;
    width: 525px;
    height: 300px;
    background: radial-gradient(ellipse at 55% 40%, #ffffff 0%, var(--card) 55%, var(--card-edge) 100%);
    box-shadow: 0 6px 18px rgba(0,0,0,.45);
  }
  .card--front { left: 58px; }
  .card--back { left: 617px; }

  .contact {
    position: absolute;
    left: 225px;
    top: 24px;
  }
  .contact__name {
    color: var(--navy);
    font-size: 17px;
    font-weight: 600;
    letter-spacing: .06em;
    text-transform: uppercase;
    line-height: 1.2;
  }
  .contact__title {
    color: var(--ink);
    font-size: 10px;
    letter-spacing: .08em;
    text-transform: uppercase;
    margin-top: 2px;
  }
  .contact__list {
    list-style: none;
    margin-top: 12px;
  }
  .contact__item {
    display: flex;
    align-items: center;
    gap: 7px;
    color: var(--ink);
    font-size: 11px;
    line-height: 13px;
    margin-bottom: 4px;
  }
  .contact__label {
    display: inline-block;
    width: 52px;
    color: var(--navy);
    font-weight: 600;
  }
  .icon { width: 13px; height: 13px; flex: none; }

  .divider {
    position: absolute;
    left: 232px;
    right: 22px;
    top: 190px;
    height: 1px;
    background: var(--rule);
  }
  .address {
    position: absolute;
    left: 232px;
    top: 200px;
    display: flex;
    align-items: flex-start;
    gap: 7px;
    color: var(--ink);
    font-size: 11px;
    line-height: 15px;
    font-style: normal;
  }
  .address .icon { margin-top: 1px; }

  .brand {
    position: absolute;
    display: flex;
    align-items: center;
    gap: 8px;
    color: var(--navy);
    font-weight: 600;
    letter-spacing: .05em;
    text-transform: uppercase;
    white-space: nowrap;
  }
  .brand__mark {
    background: var(--navy);
    flex: none;
  }
  .card--front .brand { left: 26px; top: 258px; font-size: 14px; }
  .card--front .brand__mark { width: 14px; height: 14px; }
  .card--back .brand {
    left: 50%; top: 50%;
    transform: translate(-50%, -50%);
    font-size: 19px;
  }
  .card--back .brand__mark { width: 18px; height: 18px; }
</style>
</head>
<body>
  <section class="card card--front" aria-label="Card front">
    <div class="contact">
      <h1 class="contact__name">R. Daniel Hollis</h1>
      <p class="contact__title">Principal, Financial Advisor, WPSA®</p>
      <ul class="contact__list">
        <li class="contact__item">
          <svg class="icon" viewBox="0 0 16 16" aria-hidden="true"><circle cx="8" cy="8" r="8" fill="var(--icon)"/><path d="M5.3 4.2l1.5-.3.8 2-1 .7a5 5 0 0 0 2.8 2.8l.7-1 2 .8-.3 1.5c-3.5.3-6.8-3-6.5-6.5z" fill="#fff"/></svg>
          <span class="contact__label">Phone</span>646-555-0192
        </li>
        <li class="contact__item">
          <svg class="icon" viewBox="0 0 16 16" aria-hidden="true"><circle cx="8" cy="8" r="8" fill="var(--icon)"/><path d="M5.3 4.2l1.5-.3.8 2-1 .7a5 5 0 0 0 2.8 2.8l.7-1 2 .8-.3 1.5c-3.5.3-6.8-3-6.5-6.5z" fill="#fff"/></svg>
          <span class="contact__label">Office</span>646-555-0148
        </li>
        <li class="contact__item">
          <svg class="icon" viewBox="0 0 16 16" aria-hidden="true"><circle cx="8" cy="8" r="8" fill="var(--icon)"/><path d="M5.3 4.2l1.5-.3.8 2-1 .7a5 5 0 0 0 2.8 2.8l.7-1 2 .8-.3 1.5c-3.5.3-6.8-3-6.5-6.5z" fill="#fff"/></svg>
          <span class="contact__label">Toll-Free</span>800-555-0176
        </li>
        <li class="contact__item">
          <svg class="icon" viewBox="0 0 16 16" aria-hidden="true"><circle cx="8" cy="8" r="8" fill="var(--icon)"/><rect x="4.5" y="6.5" width="7" height="4" fill="#fff"/><rect x="5.8" y="4" width="4.4" height="2.5" fill="#fff"/></svg>
          <span class="contact__label">Fax</span>646-555-0133
        </li>
        <li class="contact__item">
          <svg class="icon" viewBox="0 0 16 16" aria-hidden="true"><circle cx="8" cy="8" r="8" fill="var(--icon)"/><rect x="4" y="5" width="8" height="6" fill="#fff"/><path d="M4 5l4 3.5L12 5" stroke="var(--icon)" stroke-width="1" fill="none"/></svg>
          dan@corvanecapital.example
        </li>
        <li class="contact__item">
          <svg class="icon" viewBox="0 0 16 16" aria-hidden="true"><circle cx="8" cy="8" r="8" fill="var(--icon)"/><circle cx="8" cy="8" r="4.2" fill="none" stroke="#fff" stroke-width="1"/><path d="M3.8 8h8.4M8 3.8v8.4" stroke="#fff" stroke-width="1"/></svg>
          www.corvanecapital.example
        </li>
      </ul>
    </div>
    <div class="divider"></div>
    <address class="address">
      <svg class="icon" viewBox="0 0 16 16" aria-hidden="true"><circle cx="8" cy="8" r="8" fill="var(--icon)"/><path d="M8 3.5a3 3 0 0 0-3 3c0 2.2 3 6 3 6s3-3.8 3-6a3 3 0 0 0-3-3z" fill="#fff"/><circle cx="8" cy="6.5" r="1.1" fill="var(--icon)"/></svg>
      <span>418 Brenton Street, Suite 2300<br>New York, NY 10027</span>
    </address>
    <div class="brand">
      <span class="brand__mark" aria-hidden="true"></span>
      Corvane Capital Partners, LLC
    </div>
  </section>

  <section class="card card--back" aria-label="Card back">
    <div class="brand">
      <span class="brand__mark" aria-hidden="true"></span>
      Corvane Capital Partners, LLC
    </div>
  </section>
</body>
</html>
```